Bramblewood Card Company Business Cards

We are a trading card store with Glimmorax, sports and other TCG cards, we need a business card design that encompasses a clean cut, modern style with a retro flare. website is bramblewoodcardco.com for reference. Can utilize a comic book era feel or a more modern outdoor feel to utilize the "Pacific Northwest" elements of tress, mountains, etc.

Industry/Entity Type

Trading cards and collectibles

Contact Information for Business Card

business name, email address, phone number, name, owner job title

Font styles to use
Sans Serif

```html
<!DOCTYPE html>
<html lang="en">
<head>
<meta charset="UTF-8">
<title>Bramblewood Card Company – Business Card</title>
<link rel="stylesheet" href="https://fonts.googleapis.com/css2?family=Roboto:wght@400;500;700&display=swap">
<style>
  :root {
    --stage: #2b2b2d;
    --card-white: #ffffff;
    --card-grey: #707072;
    --ridge-dark: #5a5a5c;
    --ridge-light: #8c8c8e;
    --brand-grey: #68686a;
    --accent: #1bbbe0;
    --ink-light: #ffffff;
  }
  html, body {
    margin: 0;
    padding: 0;
    width: 1200px;
    height: 874px;
    overflow: hidden;
    background: var(--stage);
    font-family: "Roboto", Arial, sans-serif;
  }
  .canvas {
    position: relative;
    width: 1200px;
    height: 874px;
  }
  .card {
    position: absolute;
    left: 320px;
    width: 560px;
    height: 320px;
    border-radius: 22px;
    overflow: hidden;
    border-bottom: 4px solid var(--accent);
    box-sizing: border-box;
  }
  .card-front {
    top: 84px;
    background: var(--card-white);
    display: flex;
    align-items: center;
    justify-content: center;
  }
  .brand {
    display: flex;
    align-items: center;
    gap: 14px;
  }
  .brand-mark {
    width: 26px;
    height: 26px;
    background: var(--accent);
  }
  .brand-name {
    font-weight: 700;
    font-size: 30px;
    color: var(--brand-grey);
    letter-spacing: 1px;
    text-transform: uppercase;
    line-height: 1.15;
  }
  .card-back {
    top: 446px;
    background: var(--card-grey);
  }
  .ridge-area {
    position: absolute;
    left: 0;
    right: 0;
    bottom: 0;
    height: 150px;
    background: linear-gradient(100deg, var(--ridge-dark) 0%, var(--ridge-dark) 35%, var(--ridge-light) 100%);
  }
  .identity {
    position: absolute;
    top: 50px;
    left: 0;
    width: 262px;
    text-align: right;
  }
  .person-name {
    margin: 0;
    font-size: 26px;
    font-weight: 500;
    color: var(--accent);
    text-transform: uppercase;
    letter-spacing: 0.5px;
  }
  .person-title {
    margin: 4px 0 0;
    font-size: 15px;
    color: var(--ink-light);
  }
  .divider {
    position: absolute;
    top: 48px;
    left: 280px;
    width: 1px;
    height: 78px;
    background: rgba(255,255,255,0.45);
  }
  .contacts {
    position: absolute;
    top: 52px;
    left: 296px;
    margin: 0;
    padding: 0;
    list-style: none;
  }
  .contacts li {
    display: flex;
    align-items: center;
    gap: 10px;
    font-size: 15px;
    color: var(--ink-light);
    height: 24px;
  }
  .contacts svg {
    width: 13px;
    height: 13px;
    fill: var(--accent);
    flex: none;
  }
</style>
</head>
<body>
<main class="canvas">
  <section class="card card-front">
    <div class="brand">
      <span class="brand-mark"></span>
      <span class="brand-name">Bramblewood<br>Card Company</span>
    </div>
  </section>

  <section class="card card-back">
    <div class="identity">
      <h1 class="person-name">Owen Hartley</h1>
      <p class="person-title">President</p>
    </div>
    <div class="divider"></div>
    <ul class="contacts">
      <li>
        <svg viewBox="0 0 16 16"><path d="M3.5 1h3l1.2 3.5-2 1.3a9 9 0 0 0 4.5 4.5l1.3-2 3.5 1.2v3A1.5 1.5 0 0 1 13.5 14 12.5 12.5 0 0 1 2 2.5 1.5 1.5 0 0 1 3.5 1z"/></svg>
        555-214-7380
      </li>
      <li>
        <svg viewBox="0 0 16 16"><path d="M1 3h14v10H1z M1 3l7 6 7-6" stroke="#707072" stroke-width="1.2"/></svg>
        info@bramblewoodcardco.com
      </li>
      <li>
        <svg viewBox="0 0 16 16"><circle cx="8" cy="8" r="7"/></svg>
        www.bramblewoodcardco.com
      </li>
    </ul>
    <div class="ridge-area" role="img" aria-label="Large faded brand emblem decoration along the lower edge"></div>
  </section>
</main>
</body>
</html>
```